Hearthside Lending Relief

Please help us give our website a remake or a FACELIFT. It is not very good but it says what we need it to say. But the design is terrible.
I would like our new design font and logo to be used as the theme.

I also want more photos on the site.

I also want consistency with the pages so they look clean.

We want the professionals to do this, let's see what you got!

Thank you!
Updates

Project Deadline Extended
Reason: I can understand you want to be paid. So I will commit to the fee but I want you to have time to make a KICK ASS website for me dudes! Thanks

HI!  Just wanted to say thanks for your time on these.  A lot are great.  However the firefighters have nothing to do with Foreclosure.  We are saving peoples homes from the bank taking them and selling them.   I LOVE the house photos and the families on the website.  That is the direction we like.  THanks.

THANK U ALL FOR THE WORK!   I like a few ending in the numbers: 147  733  693  536  620  478  727  508     I will go over them and choose one soon.  Thank you.   You will be paid shortly. 

Requirements
Must have
• Bright, Upbeat photos. Color scheme should be in order. We like icons on the bottom. not just text.

```html
<!DOCTYPE html>
<html lang="en">
<head>
<meta charset="utf-8">
<title>Hearthside Lending Relief – Contact Us</title>
<link href="https://fonts.googleapis.com/css2?family=Arimo:wght@400;700&family=Tinos:wght@400;700&display=swap" rel="stylesheet">
<style>
:root{
  --red:#e8262d;
  --blue:#1a8fd0;
  --ink:#555a60;
  --ink-soft:#6b7075;
  --page:#eceef0;
  --white:#ffffff;
  --field-line:#d8dbde;
  --nav-top:#6b6e72;
  --nav-bottom:#3d4043;
  --navy-a:#0d4f8c;
  --navy-b:#062a50;
  --foot-link:#cfe0f2;
  --foot-head:#4fb0f0;
}
*{margin:0;padding:0;box-sizing:border-box}
html,body{width:815px;height:1200px;overflow:hidden}
body{position:relative;background:var(--page);font-family:"Arimo",Arial,sans-serif;color:var(--ink)}
.abs{position:absolute}

/* header */
.header{left:0;top:0;width:815px;height:146px;background:var(--white)}
.account-links{left:621px;top:0;width:88px;height:19px;background:#e4e6e8;font-size:8px;color:#777;display:flex;align-items:center;justify-content:center;gap:4px}
.brand{left:116px;top:40px;display:flex;align-items:center;gap:10px}
.brand-mark{width:58px;height:58px;border-radius:50%;background:var(--red)}
.brand-name{font-weight:700;font-size:17px;line-height:17px;color:var(--red);text-transform:uppercase;width:150px}
.hotline{left:456px;top:62px;display:flex;align-items:baseline;gap:8px}
.hotline-label{font-size:12px;color:#555}
.hotline-number{font-family:"Tinos",serif;font-size:27px;color:var(--blue)}

.main-nav{left:105px;top:105px;width:604px;height:31px;background:linear-gradient(var(--nav-top),var(--nav-bottom));display:flex;align-items:center;font-size:11px;color:#fff;text-transform:uppercase}
.main-nav .item{height:31px;display:flex;align-items:center;justify-content:center;border-right:1px solid #2f3235;padding:0 16px}
.main-nav .home{width:74px}
.main-nav .current{background:#3a3c3f}
.search{margin-left:auto;margin-right:10px;width:122px;height:19px;background:#fff;display:flex;align-items:center}
.search span{flex:1;font-size:8px;color:#888;padding-left:6px;text-transform:none}
.search .go{width:18px;height:19px;background:var(--red);display:flex;align-items:center;justify-content:center}

/* intro */
.page-title{left:105px;top:189px;font-family:"Tinos",serif;font-size:21px;color:var(--red);font-variant:small-caps;letter-spacing:.5px}
.title-rule{left:105px;top:212px;width:600px;height:1px;background:#cfd2d5}
.lang-link{left:616px;top:196px;font-size:10.5px;color:var(--blue)}

.lead{left:105px;top:258px;width:166px;font-size:9.3px;line-height:14.6px;text-align:justify;color:var(--ink)}
.lead p+p{margin-top:14px}
.lead b{color:var(--blue)}

.contact-card{left:105px;top:457px;width:190px;font-size:10px;line-height:15px}
.contact-card .org{color:var(--blue);font-weight:700;font-size:10.5px;text-transform:uppercase}
.contact-card .tag{color:var(--red);font-weight:700;margin-top:14px;display:block;text-transform:uppercase}

/* form */
.request-form{left:344px;top:253px;width:360px}
.field{display:flex;align-items:center;height:32.9px}
.field label{width:174px;font-size:11.5px;color:var(--ink-soft)}
.input{height:23px;background:var(--white);border:1px solid var(--field-line)}
.input.full{width:182px}
.input.date{width:150px}
.input.zip{width:122px}
.cal{margin-left:10px}
.hint{margin-left:9px;font-size:10px;color:#999}
.select{width:182px;height:23px;background:#fff;border:1px solid var(--field-line);display:flex;align-items:center;justify-content:space-between;font-size:8.5px;color:#888;padding-left:7px}
.select .arrow{width:17px;height:17px;background:var(--blue);margin-right:2px;display:flex;align-items:center;justify-content:center}
.comments{align-items:flex-start;height:auto;padding-top:6px}
.textarea{width:182px;height:82px;background:#fff;border:1px solid var(--field-line);font-size:8.5px;color:#999;padding:9px 8px;margin-top:-6px}
.submit{left:621px;top:875px;width:79px;height:25px;background:var(--red);border-radius:2px;color:#fff;font-family:"Tinos",serif;font-weight:700;font-size:13px;display:flex;align-items:center;justify-content:center;letter-spacing:.5px}

/* footer */
.footer{left:0;top:985px;width:815px;height:215px;background:radial-gradient(ellipse at 45% 0%,var(--navy-a),var(--navy-b) 75%)}
.foot-col{top:1028px}
.foot-col h3{font-size:13px;color:var(--foot-head);font-weight:700;margin-bottom:4px}
.foot-col li{list-style:none;font-size:7.8px;color:var(--foot-link);line-height:13px}
.newsletter-title{left:379px;top:1028px;font-size:13px;font-weight:700;color:#fff}
.email-field{left:377px;top:1054px;width:150px;height:23px;background:#fff;border-radius:3px;font-size:8.5px;color:#888;display:flex;align-items:center;padding-left:9px}
.subscribe{left:535px;top:1054px;width:74px;height:24px;background:var(--red);border-radius:3px;color:#fff;font-weight:700;font-size:11px;display:flex;align-items:center;justify-content:center}
.social{left:642px;top:1054px;display:flex;gap:4px}
.social span{width:20px;height:20px;background:#d9dde1;border-radius:3px}
.foot-rule{left:0;top:1127px;width:815px;height:1px;background:#153d68}
.legal{left:119px;top:1150px;font-size:7.8px;color:#e4edf6}
.copyright{left:119px;top:1163px;font-size:7.8px;color:var(--blue)}
</style>
</head>
<body>

<header class="abs header"></header>
<div class="abs account-links"><span>Login</span><span>|</span><span>Contacts</span></div>
<div class="abs brand"><span class="brand-mark"></span><span class="brand-name">Hearthside Lending Relief</span></div>
<div class="abs hotline"><span class="hotline-label">Call Toll-Free Now</span><span class="hotline-number">877-555-0142</span></div>

<nav class="abs main-nav">
  <div class="item home">
    <svg width="14" height="13" viewBox="0 0 14 13"><path d="M7 0 0 6h2v7h4V9h2v4h4V6h2z" fill="#fff"/></svg>
  </div>
  <div class="item">About Us</div>
  <div class="item">Services</div>
  <div class="item">Financing Options</div>
  <div class="item current">Contact Us</div>
  <div class="search"><span>Search...</span><div class="go">
    <svg width="10" height="10" viewBox="0 0 10 10"><circle cx="6" cy="4" r="3" fill="none" stroke="#fff" stroke-width="1.5"/><path d="M4 6 1 9" stroke="#fff" stroke-width="1.8"/></svg>
  </div></div>
</nav>

<h1 class="abs page-title">We’ll Be Glad to Meet You</h1>
<div class="abs title-rule"></div>
<div class="abs lang-link">Hablamos Español</div>

<div class="abs lead">
  <p>To find out more about <b>HEARTHSIDE LENDING RELIEF</b> or any of our services, please complete the form and we will be in touch as soon as possible.</p>
  <p>Please note that your information will remain confidential and will only be used to fulfill your request.</p>
</div>

<div class="abs contact-card">
  <div class="org">Hearthside Lending<br>Relief</div>
  <span class="tag">Address:</span>
  418 Harbor Street, Suite 210<br>Bayview, CA 92000<br>877-555-0142
  <span class="tag">Email:</span>
  info@hearthsidelendingrelief.com
</div>

<form class="abs request-form">
  <div class="field"><label>When Was Notice Of Default?</label><span class="input date"></span>
    <svg class="cal" width="22" height="22" viewBox="0 0 22 22"><rect x="0.5" y="0.5" width="21" height="21" rx="2" fill="#f4f4f4" stroke="#ccc"/><rect x="0.5" y="0.5" width="21" height="5" fill="var(--red)"/><g fill="#ccc"><rect x="3" y="8" width="3" height="2"/><rect x="8" y="8" width="3" height="2"/><rect x="13" y="8" width="3" height="2"/><rect x="3" y="12" width="3" height="2"/><rect x="8" y="12" width="3" height="2"/><rect x="13" y="12" width="3" height="2"/><rect x="3" y="16" width="3" height="2"/><rect x="8" y="16" width="3" height="2"/></g></svg></div>
  <div class="field"><label>When Is Trustee Sale Date?</label><span class="input date"></span>
    <svg class="cal" width="22" height="22" viewBox="0 0 22 22"><rect x="0.5" y="0.5" width="21" height="21" rx="2" fill="#f4f4f4" stroke="#ccc"/><rect x="0.5" y="0.5" width="21" height="5" fill="var(--red)"/><g fill="#ccc"><rect x="3" y="8" width="3" height="2"/><rect x="8" y="8" width="3" height="2"/><rect x="13" y="8" width="3" height="2"/><rect x="3" y="12" width="3" height="2"/><rect x="8" y="12" width="3" height="2"/><rect x="13" y="12" width="3" height="2"/><rect x="3" y="16" width="3" height="2"/><rect x="8" y="16" width="3" height="2"/></g></svg></div>
  <div class="field"><label>First Name:</label><span class="input full"></span></div>
  <div class="field"><label>Last Name:</label><span class="input full"></span></div>
  <div class="field"><label>Address 1:</label><span class="input full"></span></div>
  <div class="field"><label>Address 2:</label><span class="input full"></span></div>
  <div class="field"><label>City:</label><span class="input full"></span></div>
  <div class="field"><label>Zip Code:</label><span class="input zip"></span><span class="hint">5 digits</span></div>
  <div class="field"><label>State:</label><span class="select">Please select<span class="arrow"><svg width="9" height="7" viewBox="0 0 9 7"><path d="M0 0h9L4.5 7z" fill="#fff"/></svg></span></span></div>
  <div class="field"><label>Daytime Phone:</label><span class="input full"></span></div>
  <div class="field"><label>Evening Phone:</label><span class="input full"></span></div>
  <div class="field"><label>How Many Months Behind?</label><span class="input full"></span></div>
  <div class="field"><label>What's Your Monthly Payment?</label><span class="input full"></span></div>
  <div class="field"><label>Who Is Loan With?</label><span class="input full"></span></div>
  <div class="field"><label>What Is Your Balance?</label><span class="input full"></span></div>
  <div class="field"><label>Email:</label><span class="input full"></span></div>
  <div class="field comments"><label>Comments:</label><span class="textarea">Enter comments here...</span></div>
</form>
<div class="abs submit">SUBMIT</div>

<footer class="abs footer"></footer>
<div class="abs foot-col" style="left:119px"><h3>About Us</h3><ul><li>Company Info</li><li>Our Services</li><li>Clients</li><li>Partners</li></ul></div>
<div class="abs foot-col" style="left:218px"><h3>Advice</h3><ul><li>Sign up</li><li>Forums</li><li>Promotion</li><li>Career</li></ul></div>
<div class="abs foot-col" style="left:303px"><h3>Join In</h3><ul><li>FAQs</li><li>Solutions</li><li>Sitemap</li><li>Contacts</li></ul></div>
<div class="abs newsletter-title">Join our Newsletter</div>
<div class="abs email-field">Email Address:</div>
<div class="abs subscribe">Subscribe</div>
<div class="abs social"><span></span><span></span><span></span></div>
<div class="abs foot-rule"></div>
<div class="abs legal">Disclaimer &amp; Terms &amp; Conditions &nbsp;|&nbsp; Privacy Policy &nbsp;|&nbsp;Advertise With Us &nbsp;|&nbsp; Contact Us</div>
<div class="abs copyright">Hearthside Lending Relief © 2012. &nbsp;All Rights Reserved</div>

</body>
</html>
```